Business Card Design

My business is writing crime novels to entertain readers. I write legal thrillers and mysteries. I need a card for publishers, agents, other authors, and media.

Industry/Entity Type

Legal

Contact Information for Business Card

Paul Derrow
www.derrowfiction.example
pauljderrow@inkpost.example
0064 27 5190472

```html
<!DOCTYPE html>
<html lang="en">
<head>
<meta charset="utf-8">
<title>Paul Derrow – Business Card</title>
<link href="https://fonts.googleapis.com/css2?family=Libre+Baskerville:wght@400;700&family=Open+Sans:wght@400&display=swap" rel="stylesheet">
<style>
  :root {
    --stage: #e4e4e4;
    --card-top: #3b3b3b;
    --card-bottom: #121212;
    --ink: #ffffff;
    --ink-soft: #f2f2f2;
    --portrait-light: #f4f4f4;
    --portrait-mid: #c9c9c9;
    --portrait-dark: #6a6a6a;
  }
  * { margin: 0; padding: 0; box-sizing: border-box; }
  html, body {
    width: 1200px;
    height: 864px;
    overflow: hidden;
    background: var(--stage);
  }
  .card {
    position: absolute;
    left: 150px;
    top: 162px;
    width: 900px;
    height: 540px;
    background: linear-gradient(175deg, var(--card-top) 0%, #262626 45%, var(--card-bottom) 100%);
    box-shadow: 0 18px 40px rgba(0,0,0,0.25);
  }
  .card__name {
    position: absolute;
    left: 330px;
    top: 78px;
    width: 460px;
    text-align: center;
    font-family: "Libre Baskerville", serif;
    font-weight: 400;
    font-size: 32px;
    letter-spacing: 1px;
    text-transform: uppercase;
    color: var(--ink);
    text-shadow: 0 2px 3px rgba(0,0,0,0.6);
  }
  .card__portrait {
    position: absolute;
    left: 95px;
    top: 135px;
    width: 270px;
    height: 270px;
    border-radius: 50%;
    background: radial-gradient(circle at 50% 38%, var(--portrait-mid) 0%, var(--portrait-mid) 22%, var(--portrait-light) 40%, var(--portrait-light) 62%, var(--portrait-dark) 100%);
    box-shadow: inset 0 0 0 3px #dcdcdc;
  }
  .contact {
    position: absolute;
    left: 412px;
    top: 252px;
    list-style: none;
    font-family: "Open Sans", sans-serif;
    font-size: 23px;
    letter-spacing: 1.2px;
    color: var(--ink-soft);
  }
  .contact__item {
    display: flex;
    align-items: center;
    height: 43px;
  }
  .contact__icon {
    width: 26px;
    height: 22px;
    margin-right: 20px;
    flex: none;
  }
  .rule {
    position: absolute;
    background: var(--ink);
  }
  .rule--short { left: 412px; top: 392px; width: 395px; height: 14px; }
  .rule--long  { left: 155px; top: 490px; width: 652px; height: 16px; }
</style>
</head>
<body>
  <div class="card">
    <h1 class="card__name">Paul Derrow</h1>
    <div class="card__portrait" role="img" aria-label="Portrait photo of the author"></div>

    <ul class="contact">
      <li class="contact__item">
        <svg class="contact__icon" viewBox="0 0 26 22" aria-hidden="true">
          <rect x="2" y="2" width="22" height="14" fill="none" stroke="#fff" stroke-width="2.2"/>
          <rect x="10" y="16" width="6" height="3" fill="#fff"/>
          <rect x="7" y="19" width="12" height="2" fill="#fff"/>
        </svg>
        <span>www.derrowfiction.example</span>
      </li>
      <li class="contact__item">
        <svg class="contact__icon" viewBox="0 0 26 22" aria-hidden="true">
          <rect x="2" y="4" width="22" height="15" fill="#fff"/>
          <path d="M2 4 L13 13 L24 4" fill="none" stroke="#1a1a1a" stroke-width="1.8"/>
          <path d="M2 19 L10 11 M24 19 L16 11" fill="none" stroke="#1a1a1a" stroke-width="1.4"/>
        </svg>
        <span>pauljderrow@inkpost.example</span>
      </li>
      <li class="contact__item">
        <svg class="contact__icon" viewBox="0 0 26 22" aria-hidden="true">
          <path d="M3 8 Q13 0 23 8 L21 11 L17 9 L17 7 Q13 5 9 7 L9 9 L5 11 Z" fill="#fff"/>
          <path d="M7 12 L19 12 L22 20 L4 20 Z" fill="#fff"/>
          <circle cx="13" cy="16" r="2.4" fill="#1a1a1a"/>
        </svg>
        <span>0064 27 5190472</span>
      </li>
    </ul>

    <div class="rule rule--short"></div>
    <div class="rule rule--long"></div>
  </div>
</body>
</html>
```